Lantern Petals Website v.1 - attract floral shop franchisees

I need a simple information website for my new business. We are a franchisor of flower shops. The overall purpose of the website is to promote the company and the service, especially to potential franchisees and retailers. Only about 4 pages are required including homepage, About, For Supermarkets, For Franchisees, and Contact. No special functions are required except the site will have two separate inquiry forms that must be filled out online and submitted via automated email. Similarly, an email form should be linked from the Contact page. I have a logo and business cards designed by ArtMingle, and I would like the site to have a consistent color scheme and style. The key to design will be to express the joy and love associated with flowers and floral bouquets.
IMPORTANT - I will be exporting the website design to Wordpress CMS in a site hosted by HostNimbus. For smooth integration into WordPress hosted by HostNimbus, the designer should build the site using a WordPress-friendly format. Ideally, they should use HTML, CSS, and PHP. Creating a custom theme or using a page builder that exports to WordPress-compatible files is best. This ensures the site can be easily imported and managed within WordPress.

Target Market(s)

Potential franchisees (existing florists or creative types who might like to own a floral business) and supermarkets who might want us to run their floral department

Industry/Entity Type

Floral retailing

Requirements
Must have
• A brand theme that is beautiful, consistent throughout and builds on the logo design
Nice to have
• Show gender and ethnic diversity in customers and florists. Pictures of happy florists (for franchisees) and pictures of amazing floral department displays (for supermarkets)

```html
<!DOCTYPE html>
<html lang="en">
<head>
<meta charset="utf-8">
<title>Lantern Petals – Floral Franchising</title>
<link href="https://fonts.googleapis.com/css2?family=Playfair+Display:wght@400;500&family=Montserrat:wght@400;500;600;700&family=Pacifico&display=swap" rel="stylesheet">
<style>
:root{
  --green:#0c7a3c;
  --green-dark:#0a6a33;
  --orange:#e07b37;
  --mint:#e6efe6;
  --mint-2:#dfeadb;
  --ink:#1f1f1f;
  --muted:#555;
  --line:#d7d7d7;
  --white:#fff;
}
*{box-sizing:border-box;margin:0;padding:0}
html,body{width:1200px;height:4087px;overflow:hidden}
body{font-family:"Montserrat",sans-serif;color:var(--ink);background:var(--white);position:relative}
.abs{position:absolute}
.serif{font-family:"Playfair Display",serif;font-weight:400}
.btn{position:absolute;display:flex;align-items:center;justify-content:center;color:#fff;font-size:11px;font-weight:600;border-radius:3px;box-shadow:0 6px 14px rgba(0,0,0,.15)}
.btn.green{background:var(--green)}
.btn.orange{background:var(--orange)}
.eyebrow{font-size:10px;color:var(--orange);letter-spacing:.3px;text-transform:uppercase}
.photo{position:absolute}

/* header */
.site-header{position:absolute;left:0;top:0;width:1200px;height:67px;border-top:3px solid var(--green);background:#fff}
.brand{position:absolute;left:130px;top:14px;display:flex;align-items:center;gap:8px;font-family:"Playfair Display",serif;font-size:20px;color:var(--orange)}
.brand .dot{width:22px;height:22px;border-radius:50%;background:var(--orange)}
.nav{position:absolute;left:484px;top:26px;display:flex;gap:34px;font-size:10px;color:#333}
.nav span::after{content:" ⌄";font-size:9px}
.nav-cta{left:968px;top:18px;width:100px;height:30px;border-radius:2px;box-shadow:none}

/* hero */
.hero{position:absolute;left:0;top:67px;width:1200px;height:492px}
.slide-left{left:0;top:0;width:194px;height:492px;background:linear-gradient(90deg,#d9d6d2,#eeebe7)}
.slide-main{left:217px;top:0;width:783px;height:492px;background:linear-gradient(90deg,#f4f4f3,#e9e9e8)}
.slide-main .photo{left:370px;top:0;width:413px;height:492px;background:linear-gradient(160deg,#e6e4e1 0%,#cdbfbf 45%,#7a5b54 70%,#e9c2c6 100%)}
.slide-right{left:1024px;top:0;width:176px;height:492px;background:linear-gradient(90deg,#f5e1d6,#f0d3c4)}
.hero h1{font-family:"Playfair Display",serif;font-weight:400;font-size:47px;line-height:50px;color:#222}
.arrow{position:absolute;width:50px;height:50px;border-radius:50%;background:#fff;box-shadow:0 4px 12px rgba(0,0,0,.12);display:flex;align-items:center;justify-content:center}

/* benefits band */
.benefits{position:absolute;left:0;top:575px;width:1200px;height:406px;background:var(--mint)}
.center{text-align:center;left:0;width:1200px}
.feature{position:absolute;top:154px;display:flex;align-items:center;gap:12px}
.feature .ring{width:57px;height:57px;border-radius:50%;border:2px solid var(--green);display:flex;align-items:center;justify-content:center}
.feature b{display:block;font-size:11px;font-weight:600;color:#222}
.feature small{display:block;font-size:9px;color:#999;margin-top:5px}

/* sections */
.section-title{font-family:"Playfair Display",serif;font-size:31px;font-weight:400}
.body-copy{font-size:11.5px;line-height:15px;color:#444}
.split-title{font-family:"Playfair Display",serif;font-size:31px;line-height:34px;font-weight:400}

/* sale */
.sale{position:absolute;left:0;top:2200px;width:1200px;height:404px;background:linear-gradient(90deg,#e4ecdf,#dce8d6)}
.spring{font-family:"Pacifico",cursive;color:var(--green);font-size:84px;line-height:1}

/* gallery */
.g{position:absolute}

/* contact */
.field-label{position:absolute;font-size:8px;font-weight:600;color:#333}
.field{position:absolute;border:1px solid var(--line);border-radius:3px;font-size:7px;color:#aaa;padding:13px 18px}
.info-row{display:flex;align-items:center;gap:10px;font-size:11.5px;color:#333;margin-bottom:12px}
.info-row b{font-weight:600}

/* footer */
.site-footer{position:absolute;left:0;top:3837px;width:1200px;height:250px;background:var(--green)}
.social{position:absolute;top:150px;width:28px;height:28px;border-radius:50%;background:rgba(255,255,255,.25)}
</style>
</head>
<body>

<header class="site-header">
  <div class="brand"><span class="dot"></span>Lantern Petals</div>
  <nav class="nav"><span>About Us</span><span>For Supermarkets</span><span>For Franchisees</span><span>Our Gallery</span></nav>
  <div class="btn green nav-cta">Contact Us</div>
</header>

<section class="hero">
  <div class="abs slide-left" role="img" aria-label="Florist in a striped apron holding flowers"></div>
  <div class="abs slide-main">
    <div class="photo" role="img" aria-label="Smiling florist arranging a bouquet in a flower shop"></div>
    <div class="abs eyebrow" style="left:58px;top:124px">Lantern Petals</div>
    <h1 class="abs" style="left:58px;top:145px">Fresh Flowers<br>Convey Special<br>Sentiments</h1>
    <p class="abs" style="left:61px;top:312px;font-size:11.5px;color:#444">love, happiness, joy – which every person deserves.</p>
    <div class="btn green" style="left:62px;top:350px;width:137px;height:34px">Get Started Now!</div>
  </div>
  <div class="abs slide-right">
    <div class="abs eyebrow" style="left:58px;top:124px;white-space:nowrap">For Supermarkets</div>
    <h1 class="abs" style="left:55px;top:145px;white-space:nowrap">Supermarket<br>Flower<br>Benefits</h1>
    <p class="abs" style="left:61px;top:312px;font-size:11.5px;color:#444;white-space:nowrap">love, happiness, joy</p>
    <div class="btn orange" style="left:62px;top:350px;width:137px;height:34px">Get Started Now!</div>
  </div>
  <div class="arrow" style="left:179px;top:221px"><svg width="20" height="12" viewBox="0 0 20 12"><path d="M19 6H2M7 1 2 6l5 5" fill="none" stroke="#e07b37" stroke-width="1.8"/></svg></div>
  <div class="arrow" style="left:984px;top:221px"><svg width="20" height="12" viewBox="0 0 20 12"><path d="M1 6h17M13 1l5 5-5 5" fill="none" stroke="#e07b37" stroke-width="1.8"/></svg></div>
</section>

<section class="benefits">
  <div class="abs" role="img" aria-label="Pink flower" style="left:0;top:98px;width:48px;height:92px;border-radius:0 46px 46px 0;background:radial-gradient(circle at 20% 50%,#e9557d,#f3a9bd)"></div>
  <div class="abs" role="img" aria-label="Bouquet of roses and green leaves" style="left:1014px;top:0;width:186px;height:406px;background:linear-gradient(180deg,rgba(230,239,230,0),#c9dcc2 30%,#e59b88 60%,#d9475a 85%,#e6efe6)"></div>
  <h2 class="abs center section-title" style="top:56px">Renewal, Termination &amp; Transfer</h2>
  <p class="abs center" style="top:105px;font-size:11.5px;color:#444">Terms of the Franchise Agreement. Conditions for Renewal and Extension.</p>
  <div class="feature" style="left:263px">
    <div class="ring"><svg width="30" height="22" viewBox="0 0 30 22"><rect x="1" y="3" width="17" height="12" fill="none" stroke="#0c7a3c" stroke-width="1.6"/><path d="M18 7h6l4 4v4H18" fill="none" stroke="#0c7a3c" stroke-width="1.6"/><circle cx="7" cy="18" r="2.5" fill="none" stroke="#0c7a3c" stroke-width="1.6"/><circle cx="23" cy="18" r="2.5" fill="none" stroke="#0c7a3c" stroke-width="1.6"/></svg></div>
    <div><b>FREE SHIPPING</b><small>Free shipping all order</small></div>
  </div>
  <div class="feature" style="left:505px">
    <div class="ring" style="font-size:11px;font-weight:700;color:var(--green)">24/7</div>
    <div><b>SUPPORT 24/7</b><small>Support 24 hours a day</small></div>
  </div>
  <div class="feature" style="left:749px">
    <div class="ring"><svg width="26" height="24" viewBox="0 0 26 24"><path d="M1 2h4l3 13h13l3-9H7" fill="none" stroke="#0c7a3c" stroke-width="1.6"/><circle cx="10" cy="20" r="2" fill="#0c7a3c"/><circle cx="19" cy="20" r="2" fill="#0c7a3c"/></svg></div>
    <div><b>ORDER DISCOUNT</b><small>On every order over $15.</small></div>
  </div>
  <p class="abs center" style="top:236px;font-size:18px;color:#222">Include Benefits Shown Below!</p>
  <svg class="abs" style="left:694px;top:262px" width="36" height="46" viewBox="0 0 36 46"><path d="M4 42c14-6 24-18 22-30-1-8-10-9-12-2-2 9 12 10 18 0" fill="none" stroke="#0c7a3c" stroke-width="1.6"/></svg>
  <div class="btn green" style="left:530px;top:296px;width:138px;height:34px">Receive Benefits</div>
</section>

<section>
  <div class="abs" role="img" aria-label="Green leaf sprig" style="left:0;top:1092px;width:128px;height:160px;background:radial-gradient(ellipse at 30% 50%,#3f8a3a,rgba(255,255,255,0) 70%)"></div>
  <div class="abs" role="img" aria-label="Green leaf sprig" style="left:1094px;top:1184px;width:106px;height:150px;background:radial-gradient(ellipse at 70% 50%,#3f8a3a,rgba(255,255,255,0) 70%)"></div>
  <h2 class="abs center section-title" style="top:1043px">About Lantern Petals</h2>
  <div class="abs body-copy" style="left:305px;top:1095px;width:590px;text-align:center">
    <p>Fresh flowers convey special sentiments - love, happiness, joy – which every person deserves. Lantern Petals is an entrepreneurial company created to make top quality fresh flowers and artisan-designed bouquets accessible to every consumer at affordable prices.</p>
    <p style="margin-top:15px">Lantern Petals brings the best of professional florists and supermarkets together for the benefit of consumers. It supports a national network of franchisees who own and operate the floral departments of some of the country's most progressive supermarkets, selling the finest floral stems and bouquets to customers at the market's best value.</p>
  </div>
  <div class="btn orange" style="left:530px;top:1246px;width:138px;height:32px">More About Us</div>
</section>

<section>
  <div class="abs eyebrow" style="left:168px;top:1409px;color:var(--green)">For Supermarkets</div>
  <h2 class="abs split-title" style="left:168px;top:1428px">Supermarket Flower<br>Departments Benefit</h2>
  <p class="abs body-copy" style="left:168px;top:1512px;width:410px">However their quality of stems and bouquets is often poor and in-store service is limited. In contrast, professional florists typically sell the finest quality stems, design the most beautiful bouquets and provide the finest customer service, but their costs and customer prices are high. Supermarkets find that Lantern Petals, through their florist franchise network, is able to improve their financial outcomes, provide attentive customer service and satisfaction, and lift the quality of the entire store environment.</p>
  <div class="btn green" style="left:168px;top:1658px;width:176px;height:34px">More For Supermarkets</div>
  <div class="photo" role="img" aria-label="Supermarket floral display of tulips in buckets" style="left:625px;top:1387px;width:357px;height:326px;background:linear-gradient(135deg,#4b4d4a,#e0622b 40%,#b8282a 70%,#5a5d58)"></div>
  <div class="photo" role="img" aria-label="Bouquet of pink roses" style="left:880px;top:1560px;width:226px;height:215px;border-radius:50%;background:radial-gradient(circle,#e8b7b5,#d48a98 55%,rgba(255,255,255,0) 72%)"></div>

  <div class="abs" style="left:156px;top:1785px;width:356px;height:330px;background:#e5e5e5"></div>
  <div class="photo" role="img" aria-label="Smiling florist standing behind colourful bouquets" style="left:171px;top:1773px;width:356px;height:328px;background:linear-gradient(180deg,#bfbcb5,#7f8e98 40%,#e6a83a 70%,#cfd8df)"></div>
  <div class="abs eyebrow" style="left:649px;top:1801px">For Franchisees</div>
  <h2 class="abs split-title" style="left:649px;top:1820px">National Network Of Owner<br>Operator Franchisees</h2>
  <p class="abs body-copy" style="left:649px;top:1904px;width:410px">Our franchisees are the cornerstone of our business. Many of them are already professional florists or florist employees who wish to expand their businesses without the significant costs of a traditional flower shop. Others are creative types or flower lovers who have made a career change in order to express their talents and make people happy. Still others are entrepreneurs in search of owning their own business. All are welcome if they meet Lantern Petals' high standards of quality, service and ethical business practices.</p>
  <div class="btn orange" style="left:649px;top:2051px;width:176px;height:34px">More For Franchisees</div>
</section>

<section class="sale">
  <div class="photo" role="img" aria-label="Smiling florist holding a large bouquet of protea flowers" style="left:95px;top:0;width:520px;height:404px;background:linear-gradient(120deg,#c8a59a 10%,#7a4b3b 30%,#b94a58 55%,#4b6b3e 80%,rgba(220,232,214,0))"></div>
  <div class="photo" role="img" aria-label="Large tropical leaf" style="left:985px;top:0;width:215px;height:130px;background:radial-gradient(ellipse at 70% 30%,#2f5e2e,#4e8a3e 50%,rgba(220,232,214,0) 72%)"></div>
  <div class="abs" style="left:740px;top:79px;font-size:17px;letter-spacing:1.5px;color:#333">SPECIAL OFFER</div>
  <div class="abs spring" style="left:655px;top:80px">Spring</div>
  <div class="abs" style="left:755px;top:176px;font-size:56px;font-weight:700;color:var(--orange);letter-spacing:1px">SALE</div>
  <div class="abs" style="left:740px;top:260px;font-size:17px;letter-spacing:1.5px;color:#333">UP TO 70% OFF</div>
  <svg class="abs" style="left:906px;top:253px" width="36" height="46" viewBox="0 0 36 46"><path d="M4 42c14-6 24-18 22-30-1-8-10-9-12-2-2 9 12 10 18 0" fill="none" stroke="#0c7a3c" stroke-width="1.6"/></svg>
  <div class="btn green" style="left:750px;top:302px;width:138px;height:32px">Receive Benefits</div>
</section>

<section>
  <div class="abs" role="img" aria-label="Green leaf sprig" style="left:1072px;top:2790px;width:128px;height:190px;background:radial-gradient(ellipse at 70% 50%,#3f8a3a,rgba(255,255,255,0) 70%)"></div>
  <div class="abs" role="img" aria-label="Blurred green leaves" style="left:0;top:2960px;width:80px;height:240px;background:radial-gradient(ellipse at 10% 50%,#7fa86f,rgba(255,255,255,0) 70%)"></div>
  <h2 class="abs center section-title" style="top:2678px">Our Gallery</h2>
  <p class="abs body-copy" style="left:360px;top:2733px;width:480px;text-align:center">Inspirational photos highlighting store layouts, product displays, and customer experiences.</p>
  <div class="g" role="img" aria-label="Pink and white daisies" style="left:129px;top:2817px;width:241px;height:224px;background:linear-gradient(135deg,#e77fa6,#3d6a33 50%,#e25a88)"></div>
  <div class="g" role="img" aria-label="Rows of red flowers in a greenhouse" style="left:387px;top:2830px;width:170px;height:158px;background:linear-gradient(180deg,#8a9a7d,#b3343a 60%,#3e5c32)"></div>
  <div class="g" role="img" aria-label="Shop owner among bouquets" style="left:571px;top:2793px;width:243px;height:195px;background:linear-gradient(90deg,#6a4a30,#c9b9a6 55%,#8a6a4c)"></div>
  <div class="g" role="img" aria-label="Deep pink roses with foliage" style="left:828px;top:2830px;width:170px;height:158px;background:linear-gradient(135deg,#2f4a2c,#a0264e 55%,#3d5c33)"></div>
  <div class="g" role="img" aria-label="Single pink camellia" style="left:200px;top:3058px;width:170px;height:157px;background:radial-gradient(circle,#f5a3bd,#e56b94 40%,#2f4a2c 75%)"></div>
  <div class="g" role="img" aria-label="Hydrangea and rose bouquet" style="left:387px;top:2999px;width:241px;height:224px;background:linear-gradient(180deg,#eef0ea,#d6547a 60%,#3b5a36)"></div>
  <div class="g" role="img" aria-label="Mixed pink bouquet" style="left:643px;top:3004px;width:171px;height:159px;background:linear-gradient(135deg,#d9507a,#4d6a3f 55%,#e88aa5)"></div>
  <div class="g" role="img" aria-label="Orange pincushion protea" style="left:828px;top:2999px;width:242px;height:224px;background:radial-gradient(circle at 55% 60%,#f2b42a,#c96a24 35%,#3c4a2c 70%)"></div>
  <div class="btn orange" style="left:512px;top:3272px;width:176px;height:34px">More Our Gallery</div>
</section>

<section>
  <div class="abs" role="img" aria-label="Faint pale leaf" style="left:0;top:3390px;width:120px;height:360px;background:radial-gradient(ellipse at 20% 50%,#d9e8d8,rgba(255,255,255,0) 70%)"></div>
  <div class="abs" role="img" aria-label="Tropical leaf" style="left:1080px;top:3620px;width:120px;height:217px;background:radial-gradient(ellipse at 80% 60%,#2f5e2e,#4e8a3e 45%,rgba(255,255,255,0) 72%)"></div>
  <div class="field-label" style="left:182px;top:3448px">First Name</div>
  <div class="field" style="left:178px;top:3463px;width:200px;height:37px">Type Name...</div>
  <div class="field-label" style="left:404px;top:3448px">Last Name</div>
  <div class="field" style="left:400px;top:3463px;width:200px;height:37px">Type Name...</div>
  <div class="field-label" style="left:182px;top:3513px">Email Address</div>
  <div class="field" style="left:178px;top:3528px;width:200px;height:37px">Type Email...</div>
  <div class="field-label" style="left:404px;top:3513px">Phone Number</div>
  <div class="field" style="left:400px;top:3528px;width:200px;height:37px">Type Number...</div>
  <div class="field-label" style="left:182px;top:3579px">Message</div>
  <div class="field" style="left:178px;top:3594px;width:422px;height:72px">Type Message...</div>
  <div class="btn orange" style="left:184px;top:3696px;width:176px;height:33px">Submit Request</div>

  <div class="abs eyebrow" style="left:649px;top:3452px">Contact Us</div>
  <h2 class="abs section-title" style="left:649px;top:3470px;font-size:29px">Get In Touch</h2>
  <p class="abs body-copy" style="left:649px;top:3518px;width:410px">For more information about becoming a franchisee with us, please reach out:</p>
  <div class="abs" style="left:654px;top:3566px">
    <div class="info-row"><svg width="12" height="12" viewBox="0 0 12 12"><path d="M2 1l2 0 1 3-1.5 1a7 7 0 0 0 3.5 3.5L8 7l3 1v2c0 .6-.4 1-1 1A10 10 0 0 1 1 2c0-.6.4-1 1-1z" fill="#0c7a3c"/></svg><span><b>Phone:</b> (555) 014-2290</span></div>
    <div class="info-row"><svg width="12" height="10" viewBox="0 0 12 10"><rect x="0" y="0" width="12" height="10" rx="1" fill="#0c7a3c"/><path d="M1 1l5 4 5-4" fill="none" stroke="#fff" stroke-width="1"/></svg><span><b>Email:</b> info@lanternpetals.com</span></div>
    <div class="info-row"><svg width="12" height="14" viewBox="0 0 12 14"><path d="M6 0a5 5 0 0 1 5 5c0 4-5 9-5 9S1 9 1 5a5 5 0 0 1 5-5z" fill="#0c7a3c"/><circle cx="6" cy="5" r="2" fill="#fff"/></svg><span><b>Address:</b> 48 Petal Lane, Garden Vale, FL 32145</span></div>
  </div>
  <p class="abs" style="left:649px;top:3656px;width:420px;font-size:10px;line-height:15px;color:#555">Our team is here to answer your questions and guide you through the franchising process. We look forward to hearing from you!</p>
</section>

<footer class="site-footer">
  <div class="abs" style="left:0;top:50px;width:1200px;display:flex;justify-content:center;align-items:center;gap:12px;font-family:'Playfair Display',serif;font-size:30px;color:#fff">
    <span style="width:34px;height:34px;border-radius:50%;background:#fff;display:block"></span>Lantern Petals
  </div>
  <div class="social" style="left:530px"></div>
  <div class="social" style="left:567px"></div>
  <div class="social" style="left:604px"></div>
  <div class="social" style="left:641px"></div>
  <div class="abs" style="left:185px;top:208px;width:830px;border-top:1px solid rgba(255,255,255,.25)"></div>
  <div class="abs" style="left:185px;top:226px;font-size:10px;color:#fff">© 2024 Lantern Petals, All rights reserved</div>
  <div class="abs" style="left:820px;top:226px;font-size:10px;color:#fff">Terms &amp; conditions</div>
  <div class="abs" style="left:956px;top:226px;font-size:10px;color:#fff">Privacy policy</div>
</footer>

</body>
</html>
```